Wordpress theme website for professionals working together

My partner and I are offering business services, my wife in the energy business as mainly as member of the board of commissioners. I am working as interim manager/consultant in the accounting and finance area. Both activities are connected in one company VELMOT BV (dutch ltd). We need a CV based website. Beside this we do some financial and accounting services.

Target Market(s)

small medium business

Font styles to use
Sans Serif

Colors

Designer to choose colors to be used in the design.

Requirements
Must have
• Pictures of both members.
• CLEAN AND SIMPLE
• I LIKE BLACK & WHITE
Nice to have
• I like design like this theme: http://theme.pruxelo-example.com/resume/

```html
<!DOCTYPE html>
<html lang="en">
<head>
<meta charset="utf-8">
<title>VELMOT BV – Maarten, Financial Advisor</title>
<link href="https://fonts.googleapis.com/css2?family=Poppins:wght@400;500;600;700&display=swap" rel="stylesheet">
<style>
:root{
  --black:#111111;
  --ink:#1c1c1c;
  --text:#555555;
  --muted:#777777;
  --white:#ffffff;
  --soft:#f2f2f2;
  --line:#cfcfcf;
  --ring:#e6e6e6;
}
*{box-sizing:border-box;margin:0;padding:0}
html,body{width:1200px;height:3922px;overflow:hidden}
body{font-family:'Poppins',Arial,sans-serif;color:var(--ink);background:var(--white);position:relative}

/* nav */
.site-header{position:absolute;left:0;top:0;width:1200px;height:86px;z-index:3}
.brand{position:absolute;left:123px;top:24px;font-size:30px;font-weight:400;letter-spacing:3px;color:var(--black)}
.main-nav{position:absolute;right:128px;top:32px;display:flex;gap:30px;font-size:15px;font-weight:500}
.main-nav a{color:var(--black);text-decoration:none}

/* hero */
.hero{position:absolute;left:0;top:0;width:1200px;height:727px;background:linear-gradient(90deg,#f4f4f4 0%,#ececec 45%,#dcdcdc 100%)}
.hero-photo{position:absolute;left:520px;top:0;width:680px;height:727px;background:radial-gradient(ellipse at 60% 40%,#c9b0a4 0%,#a99a92 30%,#6f7480 65%,#3c4250 100%)}
.hero-name{position:absolute;left:107px;top:262px;font-size:90px;font-weight:600;line-height:1;color:var(--black)}
.hero-role{position:absolute;left:110px;top:378px;font-size:32px;font-weight:400;color:var(--black)}
.partner-avatar{position:absolute;left:112px;top:470px;width:84px;height:84px;border-radius:50%;border:4px solid var(--white);background:linear-gradient(135deg,#8a6a5a,#c8a894)}
.partner-name{position:absolute;left:212px;top:480px;font-size:19px}
.partner-link{position:absolute;left:212px;top:510px;font-size:14px;text-decoration:underline;color:var(--black)}
.arrow{position:absolute;width:36px;height:36px;border-radius:50%;display:flex;align-items:center;justify-content:center}
.arrow.light{background:#c4c4c4}
.arrow.dark{background:var(--black)}

/* sections */
.section-title{position:absolute;left:0;width:1200px;text-align:center;font-size:44px;font-weight:500;color:var(--black)}
.education-card{position:absolute;left:73px;top:651px;width:1051px;height:408px;background:var(--white);box-shadow:0 4px 18px rgba(0,0,0,.12)}
.edu-box{position:absolute;top:110px;width:463px;height:238px;background:var(--black);color:var(--white);padding:28px 34px}
.edu-box h3{font-size:26px;font-weight:500;margin-bottom:16px}
.edu-box p{font-size:14px;line-height:24px;color:#e8e8e8}
.edu-box.right-aligned{text-align:right}
.btn-outline{position:absolute;top:150px;width:164px;height:42px;border:2px solid var(--white);border-radius:21px;font-size:14px;font-weight:500;display:flex;align-items:center;justify-content:center}

.skills{position:absolute;left:0;top:1129px;width:1200px;height:523px;background:var(--soft)}
.skill{position:absolute;top:200px;width:240px;text-align:center}
.skill svg{display:block;margin:0 auto}
.skill-label{font-size:20px;font-weight:500;margin-top:24px}

.portfolio-item{position:absolute;top:1806px;width:288px;text-align:center}
.portfolio-image{width:288px;height:189px}
.portfolio-item h3{font-size:27px;font-weight:500;margin-top:28px}
.portfolio-item p{font-size:13px;line-height:22px;color:var(--text);margin-top:8px;padding:0 12px}

.experience{position:absolute;left:0;top:2227px;width:1200px;height:1111px;background:var(--soft)}
.timeline-line{position:absolute;left:598px;top:201px;width:2px;height:785px;background:var(--line)}
.timeline-dot{position:absolute;left:589px;width:20px;height:20px;border-radius:50%;background:var(--black)}
.entry{position:absolute;width:370px}
.entry.right{left:674px}
.entry.left{left:145px;text-align:right}
.entry h3{font-size:22px;font-weight:500;color:var(--black);margin-bottom:10px}
.entry h4{font-size:16px;font-weight:500;color:#444;margin-bottom:6px}
.entry p{font-size:13px;line-height:22px;color:var(--text);margin-bottom:16px}
.entry .plain{font-size:16px;color:#555;line-height:24px}

.contact{position:absolute;left:0;top:3338px;width:1200px;height:584px;background:var(--black);color:var(--white)}
.contact h2{position:absolute;left:112px;top:58px;font-size:50px;font-weight:600}
.contact-text{position:absolute;left:112px;top:150px;width:410px;font-size:14px;line-height:27px}
.contact-detail{position:absolute;left:112px;font-size:15px}
.field{position:absolute;left:651px;width:431px;background:var(--white);color:#999;font-size:13px;padding:14px 20px}
.btn-submit{position:absolute;left:910px;top:413px;width:170px;height:42px;border:2px solid var(--white);border-radius:21px;font-size:16px;font-weight:500;display:flex;align-items:center;justify-content:center}
.social{position:absolute;top:488px;width:20px;height:20px;border-radius:50%;border:1.5px solid #bbb}
.copyright{position:absolute;left:0;top:526px;width:1200px;text-align:center;font-size:13px;color:#ddd}
</style>
</head>
<body>

<section class="hero">
  <div class="hero-photo" role="img" aria-label="Portrait photograph of Maarten, financial advisor, wearing glasses"></div>
  <h1 class="hero-name">Maarten</h1>
  <p class="hero-role">Financial Advisor</p>
  <div class="partner-avatar" role="img" aria-label="Small portrait photograph of partner Lieke"></div>
  <span class="partner-name">Lieke</span>
  <a class="partner-link">Click here</a>
  <div class="arrow light" style="left:37px;top:361px"><svg width="12" height="12" viewBox="0 0 12 12"><path d="M8 2 4 6l4 4" fill="none" stroke="#fff" stroke-width="2"/></svg></div>
  <div class="arrow dark" style="left:1124px;top:361px"><svg width="12" height="12" viewBox="0 0 12 12"><path d="M4 2l4 4-4 4" fill="none" stroke="#fff" stroke-width="2"/></svg></div>
</section>

<header class="site-header">
  <div class="brand">VELMOT BV</div>
  <nav class="main-nav"><a>Home</a><a>My Skills</a><a>Experience</a><a>Portfolio</a><a>Contact</a></nav>
</header>

<section class="education-card">
  <h2 class="section-title" style="top:26px;left:-73px">Education</h2>
  <div class="edu-box right-aligned" style="left:55px">
    <h3>Corvan (RA)</h3>
    <p>Lorem ipsum dolor sit amet, consectetur adipiscing elit,<br>sed do eiusmod tempor incididunt ut labore et</p>
    <div class="btn-outline" style="left:254px">View More</div>
  </div>
  <div class="edu-box" style="left:531px">
    <h3>Lyceum Noord</h3>
    <p>Lorem ipsum dolor sit amet, consectetur adipiscing elit,<br>sed do eiusmod tempor incididunt ut labore et</p>
    <div class="btn-outline" style="left:44px">View More</div>
  </div>
</section>

<section class="skills">
  <h2 class="section-title" style="top:62px">My Skills</h2>
  <div class="arrow light" style="left:37px;top:270px"><svg width="12" height="12" viewBox="0 0 12 12"><path d="M8 2 4 6l4 4" fill="none" stroke="#fff" stroke-width="2"/></svg></div>
  <div class="arrow dark" style="left:1124px;top:270px"><svg width="12" height="12" viewBox="0 0 12 12"><path d="M4 2l4 4-4 4" fill="none" stroke="#fff" stroke-width="2"/></svg></div>

  <div class="skill" style="left:94px">
    <svg width="172" height="172" viewBox="0 0 172 172">
      <circle cx="86" cy="86" r="80" fill="none" stroke="var(--ring)" stroke-width="6"/>
      <circle cx="86" cy="86" r="80" fill="none" stroke="var(--black)" stroke-width="6" stroke-dasharray="402 503" transform="rotate(-90 86 86)"/>
      <circle cx="86" cy="46" r="20" fill="var(--black)"/>
      <rect x="78" y="38" width="16" height="16" fill="none" stroke="#fff" stroke-width="2"/>
      <path d="M81 50v-4M86 50v-7M91 50v-5" stroke="#fff" stroke-width="2"/>
      <text x="86" y="108" text-anchor="middle" font-family="Poppins,sans-serif" font-size="30" fill="#111">80%</text>
    </svg>
    <div class="skill-label">Annual Reporting</div>
  </div>
  <div class="skill" style="left:345px">
    <svg width="172" height="172" viewBox="0 0 172 172">
      <circle cx="86" cy="86" r="80" fill="none" stroke="var(--black)" stroke-width="6"/>
      <circle cx="86" cy="46" r="20" fill="var(--black)"/>
      <circle cx="86" cy="42" r="6" fill="none" stroke="#fff" stroke-width="2"/>
      <path d="M76 56c2-6 18-6 20 0" fill="none" stroke="#fff" stroke-width="2"/>
      <text x="86" y="108" text-anchor="middle" font-family="Poppins,sans-serif" font-size="30" fill="#111">100%</text>
    </svg>
    <div class="skill-label">Accounting</div>
  </div>
  <div class="skill" style="left:599px">
    <svg width="172" height="172" viewBox="0 0 172 172">
      <circle cx="86" cy="86" r="80" fill="none" stroke="var(--ring)" stroke-width="6"/>
      <circle cx="86" cy="86" r="80" fill="none" stroke="var(--black)" stroke-width="6" stroke-dasharray="302 503" transform="rotate(-90 86 86)"/>
      <circle cx="86" cy="46" r="20" fill="var(--black)"/>
      <rect x="76" y="38" width="20" height="13" fill="none" stroke="#fff" stroke-width="2"/>
      <path d="M86 51v5M80 57h12" stroke="#fff" stroke-width="2"/>
      <text x="86" y="108" text-anchor="middle" font-family="Poppins,sans-serif" font-size="30" fill="#111">60%</text>
    </svg>
    <div class="skill-label">Financial Management</div>
  </div>
  <div class="skill" style="left:847px">
    <svg width="172" height="172" viewBox="0 0 172 172">
      <circle cx="86" cy="86" r="80" fill="none" stroke="var(--ring)" stroke-width="6"/>
      <circle cx="86" cy="86" r="80" fill="none" stroke="var(--black)" stroke-width="6" stroke-dasharray="402 503" transform="rotate(-90 86 86)"/>
      <circle cx="86" cy="46" r="20" fill="var(--black)"/>
      <circle cx="86" cy="40" r="4" fill="#fff"/><circle cx="78" cy="52" r="4" fill="#fff"/><circle cx="94" cy="52" r="4" fill="#fff"/>
      <text x="86" y="108" text-anchor="middle" font-family="Poppins,sans-serif" font-size="30" fill="#111">80%</text>
    </svg>
    <div class="skill-label">Team Player</div>
  </div>
</section>

<h2 class="section-title" style="top:1706px">Portfolio</h2>
<div class="portfolio-item" style="left:141px">
  <div class="portfolio-image" role="img" aria-label="Dramatic photograph in dark brown and red tones" style="background:radial-gradient(ellipse at 50% 50%,#8a4a2a,#2a1a12 70%)"></div>
  <h3>Fotography</h3>
  <p>Lorem ipsum dolor sit amet, consectetur adipiscing elit, sed do eiusmod tempor incididunt ut labore et dolore magna aliqua.</p>
</div>
<div class="portfolio-item" style="left:455px">
  <div class="portfolio-image" role="img" aria-label="Photograph of a businessman in a suit in a bright office" style="background:linear-gradient(90deg,#e9ecef,#8d939b 50%,#e3e6ea)"></div>
  <h3>Advisor</h3>
  <p>Lorem ipsum dolor sit amet, consectetur adipiscing elit, sed do eiusmod tempor incididunt ut labore et dolore magna aliqua.</p>
</div>
<div class="portfolio-item" style="left:771px">
  <div class="portfolio-image" role="img" aria-label="Photograph of hands working on a laptop with printed charts" style="background:linear-gradient(135deg,#b9c8d8,#eef1f5 55%,#c7a7b8)"></div>
  <h3>Controller</h3>
  <p>Lorem ipsum dolor sit amet, consectetur adipiscing elit, sed do eiusmod tempor incididunt ut labore et dolore magna aliqua.</p>
</div>

<section class="experience">
  <h2 class="section-title" style="top:60px">Experience</h2>
  <div class="timeline-line"></div>
  <div class="timeline-dot" style="top:191px"></div>
  <div class="timeline-dot" style="top:463px"></div>
  <div class="timeline-dot" style="top:834px"></div>
  <div class="timeline-dot" style="top:976px"></div>

  <div class="entry right" style="top:184px">
    <h3>Actual Jobs</h3>
    <h4>Advisor Drevon</h4>
    <p>Lorem ipsum dolor sit amet, consectetur adipiscing elit, sed do eiusmod tempor incididunt ut labore et dolore magna aliqua.</p>
    <h4>Advisor Norvik &amp; Partners</h4>
    <p>Lorem ipsum dolor sit amet, consectetur adipiscing elit, sed do eiusmod tempor incididunt ut labore et dolore magna aliqua.</p>
  </div>
  <div class="entry left" style="top:456px">
    <h3>Finished Jobs</h3>
    <h4>Controller a.i. Drevon</h4>
    <p>Lorem ipsum dolor sit amet, consectetur adipiscing elit, sed do eiusmod tempor incididunt ut labore et dolore magna aliqua.</p>
    <h4>Advisor Solvara Green</h4>
    <p>Lorem ipsum dolor sit amet, consectetur adipiscing elit, sed do eiusmod tempor incididunt ut labore et dolore magna aliqua.</p>
    <h4>Financial director Kestrel</h4>
    <p>Lorem ipsum dolor sit amet, consectetur adipiscing elit, sed do eiusmod tempor incididunt ut labore et dolore magna aliqua.</p>
  </div>
  <div class="entry right" style="top:827px">
    <h3>Worked For</h3>
    <div class="plain">Halvik Advocaten &amp; Notarissen<br>Brennel Audit</div>
  </div>
  <div class="entry left" style="top:969px">
    <h3>Other</h3>
    <div class="plain">Fotography</div>
  </div>
</section>

<section class="contact">
  <h2>Contact Us</h2>
  <p class="contact-text">Lorem ipsum dolor sit amet, consectetur adipiscing elit, sed do eiusmod tempor incididunt ut labore et dolore magna aliqua. Ut enim ad minim veniam, quis nostrud exercitation ullamco laboris nisi ut aliquip ex ea commodo consequat.</p>
  <div class="contact-detail" style="top:314px">info@velmot-example.com</div>
  <div class="contact-detail" style="top:348px">Tel: 1-800-000-0000</div>

  <div class="field" style="top:84px;height:55px">Name</div>
  <div class="field" style="top:144px;height:55px">Email</div>
  <div class="field" style="top:204px;height:55px">Subject</div>
  <div class="field" style="top:264px;height:123px">Message</div>
  <div class="btn-submit">Submit</div>

  <div class="social" style="left:539px"></div>
  <div class="social" style="left:573px"></div>
  <div class="social" style="left:607px"></div>
  <div class="social" style="left:641px"></div>
  <div class="copyright">© 2018 Copyrights | All Rights Reserved</div>
</section>

</body>
</html>
```